Design a Book Cover for a Bill Tracker Logbook

We are looking for a designer to create a book cover for a bill tracker. The detailed instructions and interior pages are attached. For those who are new to TRV, the cover template is also attached.
Please be creative and focus on creating a trustworthy, reliable, modern, and secure feeling based on the theme. You are allowed to use downloaded templates, but you must provide commercial licenses.
Attention: We are happy to pay extra tip if you are selected with a really high quality design.
US

```html
<!DOCTYPE html>
<html lang="en">
<head>
<meta charset="utf-8">
<title>Bill Tracker &amp; Password Log – Cover Wrap</title>
<link rel="stylesheet" href="https://fonts.googleapis.com/css2?family=Bodoni+Moda:wght@400&family=Open+Sans:wght@400;700&family=Cormorant+Garamond:wght@500&display=swap">
<style>
  :root{
    --stage:#b2b2b2;
    --navy-deep:#0b2347;
    --navy:#123a6e;
    --blue:#1d68aa;
    --ink-white:#ffffff;
    --page:#8fa3c1;
    --page-head:#7285a3;
    --page-line:#1e2a3c;
    --page-ink:#1c2433;
    --badge:#1a2233;
    --badge-ring:#9aa3b0;
  }
  *{margin:0;padding:0;box-sizing:border-box}
  html,body{width:1200px;height:1200px;overflow:hidden;background:var(--stage)}
  .cover{
    position:absolute;left:19px;top:226px;width:1162px;height:748px;overflow:hidden;
  }
  .cover__backdrop{
    position:absolute;inset:0;
    background:
      radial-gradient(ellipse 55% 60% at 45% 48%, var(--blue) 0%, rgba(29,104,170,0) 100%),
      linear-gradient(180deg, var(--navy-deep) 0%, var(--navy) 45%, #0f3363 80%, var(--navy-deep) 100%);
  }
  .copy{position:absolute;color:var(--ink-white);font-family:"Open Sans",sans-serif}
  .back-features{left:0;width:572px;top:78px;text-align:center;font-size:16px;line-height:25.5px}
  .back-thanks{left:0;width:580px;top:208px;text-align:center;font-size:15px;font-weight:700;line-height:21px}
  .spine-title{
    position:absolute;left:580px;top:66px;writing-mode:vertical-rl;
    font-family:"Cormorant Garamond",serif;font-size:8px;letter-spacing:.2px;color:var(--ink-white);
  }
  .front-title{
    position:absolute;left:620px;top:72px;color:var(--ink-white);
    font-family:"Bodoni Moda",serif;font-size:62px;line-height:58px;letter-spacing:-1px;white-space:nowrap;
  }
  .front-features{left:621px;top:207px;font-size:13px;line-height:20.5px}
  .imprint{
    position:absolute;width:72px;height:72px;border-radius:50%;
    background:var(--badge);border:3px solid var(--badge-ring);
    display:flex;align-items:center;justify-content:center;text-align:center;
    font-family:"Open Sans",sans-serif;font-size:11px;font-weight:400;color:var(--ink-white);line-height:12px;
    z-index:5;
  }
  .imprint--back{left:268px;top:632px}
  .imprint--front{left:862px;top:632px}
  .sheet{
    position:absolute;background:var(--page);color:var(--page-ink);
    box-shadow:0 4px 14px rgba(0,0,0,.35);transform-origin:top left;padding:26px 28px;
  }
  .sheet__heading{font-family:"Bodoni Moda",serif;font-size:27px;line-height:30px}
  .sheet__note{font-family:"Open Sans",sans-serif;font-style:italic;font-size:7.5px;line-height:10px;margin-top:4px}
  .sheet table{border-collapse:collapse;width:100%;margin-top:10px}
  .sheet th{background:var(--page-head);font-family:"Cormorant Garamond",serif;font-weight:500;font-size:8px;height:22px;border:1px solid var(--page-line)}
  .sheet td{height:28px;border:1px solid var(--page-line)}
  .sheet tr:nth-child(even) td{background:var(--page-head)}
  .sheet--bills{left:855px;top:212px;width:400px;height:520px;transform:rotate(17deg)}
  .sheet--passwords{left:671px;top:411px;width:425px;height:520px;transform:rotate(-10deg)}
  .sheet--contacts{left:746px;top:519px;width:430px;height:420px;transform:rotate(-2deg)}
  .sheet__meta{font-family:"Cormorant Garamond",serif;font-size:8px;margin-top:2px}
</style>
</head>
<body>
<main class="cover">
  <div class="cover__backdrop" role="img" aria-label="Close-up photograph of a paid invoice in deep blue tones"></div>

  <section class="copy back-features">
    <p>SAVE PASSWORDS AND CONTACTS</p>
    <p>TRACK PAYMENTS UP TO 8 YEARS</p>
    <p>100+ PAGES</p>
    <p>FROM 20__TO 20__</p>
  </section>
  <p class="copy back-thanks">THANK YOU FOR CHOOSING “BILL TRACKER &amp; PASSWORD LOG”,<br>PLEASE LEAVE A REVIEW ON SHELFMART IF YOU FIND IT HELPFUL<br>IN YOUR LIFE, THIS WILL HELP US PRODUCE MORE<br>HIGH-QUALITY CONTENT. THANK YOU.</p>
  <div class="imprint imprint--back">ELIAN<br>VOSS</div>

  <p class="spine-title">BILL TRACKER &amp; PASSWORD LOG</p>

  <h1 class="front-title">BILL TRACKER &amp;<br>PASSWORD LOG</h1>
  <section class="copy front-features">
    <p>SAVE PASSWORDS AND CONTACTS</p>
    <p>TRACK PAYMENTS UP TO 8 YEARS</p>
    <p>100+ PAGES</p>
    <p>FROM 20__TO 20__</p>
  </section>

  <article class="sheet sheet--bills">
    <h2 class="sheet__heading">BILL TRACKER</h2>
    <p class="sheet__meta">YEAR.......................................... MONTH..........................</p>
    <table>
      <tr><th>Bill</th><th>Due</th><th>Amount Paid</th><th>Unpaid Balance</th></tr>
      <tr><td></td><td></td><td></td><td></td></tr><tr><td></td><td></td><td></td><td></td></tr>
      <tr><td></td><td></td><td></td><td></td></tr><tr><td></td><td></td><td></td><td></td></tr>
      <tr><td></td><td></td><td></td><td></td></tr><tr><td></td><td></td><td></td><td></td></tr>
    </table>
  </article>

  <article class="sheet sheet--passwords">
    <h2 class="sheet__heading">PASSWORD LOG</h2>
    <p class="sheet__note">Please keep this log in a secure place and consider using a password manager or encryption for added security. Use under your own risk.</p>
    <table>
      <tr><th>Account</th><th>Username</th><th>Password</th><th>Notes</th></tr>
      <tr><td></td><td></td><td></td><td></td></tr><tr><td></td><td></td><td></td><td></td></tr>
      <tr><td></td><td></td><td></td><td></td></tr><tr><td></td><td></td><td></td><td></td></tr>
    </table>
  </article>

  <article class="sheet sheet--contacts">
    <h2 class="sheet__heading">CONTACTS</h2>
    <p class="sheet__note">Here you can keep a record of important contact information related to the bills, financial institutions, and other essential services.</p>
    <table>
      <tr><th>Name</th><th>Phone</th><th>E-Mail</th><th>Address/Notes</th></tr>
      <tr><td></td><td></td><td></td><td></td></tr><tr><td></td><td></td><td></td><td></td></tr>
      <tr><td></td><td></td><td></td><td></td></tr><tr><td></td><td></td><td></td><td></td></tr>
      <tr><td></td><td></td><td></td><td></td></tr>
    </table>
  </article>

  <div class="imprint imprint--front">ELIAN<br>VOSS</div>
</main>
</body>
</html>
```